Dental Website offering Continuing Educational Courses

Need a Wordpress CMS design for a dentist website which will offer continuing education courses. The design should be professional, simple and elegant. Logo versions are provided. Please follow those colors plus one or two others that will blend well. Here's examples of other sites they like - www.pulpvantage.com, www.kqtorvi.com, www.thebrightwellinstitute.com., www.plqma.org/. Please provide designs in jpg format. If selected, then final design will be required in psd format.

Target Market(s)

dentists, endodontists (root canal specialists)

Industry/Entity Type

Education

Requirements
Must have
• Combination Horizontal / Vertical navigation. Place course titles in vertical nav in a side bar on home page. List them as Course 1, Course 2 ,etc.. total of 7 courses. The header horizontal nav should be; Home, About, Courses, Doctor Name, Faculty, FAQ, Patients, Contact.
Need placeholder to accommodate one large static image just under main nav. Need web safe fonts. Need placeholder for calendar like this example www.quietharbors.org/. Need to show a dropdown menu example. Design for 1024 x 768. Need space on home page to allow for logos of external websites/ associations. These are; www.truefieldpulp.com, www.mavolix.com, www.wfk.org/, www.kintovarhq.com/kinto/. Would like to see a row of images across the bottom of the home page like the www.plqma.org site has. Would like to show a Contact Form on the home page like the "need assistance" form example on www.thebrightwellinstitute.com. Would like to create a placeholder on the home page for an image of a doctor.
Nice to have
• 3 or 4 column footer (which features sitemap, copyright, etc..). Examples in the design for the web site’s copy styling:
o through headers
o Bulleted list
o Hyperlink
o Table

```html
<!DOCTYPE html>
<html lang="en">
<head>
<meta charset="utf-8">
<title>Mavolix – Dental Continuing Education</title>
<link href="https://fonts.googleapis.com/css2?family=Arimo:wght@400;700&family=Crimson+Text:ital,wght@0,600;1,400&display=swap" rel="stylesheet">
<style>
:root{
  --page-bg:#eef2f5;
  --navy:#0a3c74;
  --brand:#0b4d94;
  --brand-dark:#083766;
  --footer-bg:#0a3566;
  --footer-mid:#1467c2;
  --footer-panel:#0c4f9c;
  --news-bg:#dde5ea;
  --text:#8a8a8a;
  --text-dark:#333;
  --accent:#6b9a2c;
  --line:#e2e6ea;
  --white:#fff;
}
*{margin:0;padding:0;box-sizing:border-box}
html,body{width:1050px;height:1200px;overflow:hidden}
body{background:var(--page-bg);font-family:"Arimo",Arial,sans-serif;color:var(--text);position:relative}
.abs{position:absolute}
.topline{left:0;top:0;width:1050px;height:6px;background:#5a5f66}
.page{left:151px;top:6px;width:751px;height:951px;background:var(--white)}
.main-nav{left:151px;top:6px;width:751px;height:31px;background:var(--navy);display:flex}
.main-nav a{color:var(--white);font-size:12px;font-weight:400;letter-spacing:.3px;text-decoration:none;display:flex;align-items:center;justify-content:center;border-right:1px solid #2c5d94;height:31px}
.header{left:161px;top:46px;width:728px;height:88px;background:var(--brand)}
.brand{left:12px;top:26px;color:var(--white);font-size:30px;font-weight:700;display:flex;align-items:center;gap:9px;line-height:36px}
.brand i{display:block;width:16px;height:16px;background:var(--white)}
.call{right:14px;top:16px;text-align:left;color:var(--white);font-family:"Crimson Text",Georgia,serif}
.call small{display:block;font-size:12.5px;letter-spacing:.5px}
.call strong{font-size:27px;font-weight:600;letter-spacing:1px}
.course-nav{left:161px;top:145px;width:154px;height:213px;background:var(--brand)}
.course-nav a{display:flex;align-items:center;height:28.8px;color:#dce8f5;font-size:14.5px;text-decoration:none;padding-left:14px;gap:18px;border-bottom:1px solid #0a447f}
.course-nav a.active{background:#083a70}
.course-nav svg{width:10px;height:12px}
.hero{left:315px;top:145px;width:574px;height:213px;background:linear-gradient(90deg,#d98a55 0%,#e8b48d 35%,#c98a62 60%,#8a6a58 85%,#5a5a60 100%)}
.news{left:161px;top:358px;width:728px;height:42px;background:var(--news-bg);display:flex;align-items:center}
.news h3{color:var(--brand-dark);font-size:14px;font-weight:400;width:117px;text-align:right;padding-right:30px}
.news p{font-size:9.5px;color:#555}
.welcome-title{left:163px;top:424px;color:var(--brand);font-size:19px;font-weight:400}
.welcome-copy{left:163px;top:455px;width:303px;font-size:9.2px;line-height:15.6px;color:#a0a0a0}
.doctor-photo{left:480px;top:446px;width:165px;height:110px;border:1px solid #ccc;padding:4px;background:var(--white);box-shadow:0 2px 3px rgba(0,0,0,.15)}
.doctor-photo div{width:100%;height:100%;background:linear-gradient(90deg,#3a5680,#b8c6d4 50%,#e8dcd0)}
.btn-read{left:563px;top:611px;width:71px;height:21px;border:1px solid #d8dde2;border-radius:3px;background:linear-gradient(#fff,#e9edf0);color:var(--brand-dark);font-size:9.5px;font-weight:700;display:flex;align-items:center;justify-content:center}
.hr{left:151px;top:644px;width:509px;height:1px;background:var(--line)}
.vr{left:660px;top:400px;width:1px;height:430px;background:var(--line)}
.calendar{left:688px;top:412px;width:180px}
.cal-head{height:27px;background:#2a2a2a;border-radius:3px 3px 0 0;color:var(--white);font-size:11px;font-weight:700;display:flex;align-items:center;justify-content:space-between;padding:0 10px}
.cal-days,.cal-grid{display:grid;grid-template-columns:repeat(7,1fr)}
.cal-days span{font-size:7.5px;color:#777;text-align:center;height:14px;line-height:14px;background:#f2f2f2}
.cal-grid span{height:25px;font-size:9.5px;color:#333;display:flex;align-items:center;justify-content:center;background:linear-gradient(#fafafa,#e6e6e6);border:1px solid #fff;position:relative}
.cal-grid .off{color:#bbb}
.cal-grid .today{background:#444;color:#fff}
.cal-grid .sel{background:#d4d4d4}
.cal-grid .dot::after{content:"";position:absolute;top:3px;right:5px;width:4px;height:4px;border-radius:50%;background:#333}
.cal-grid .dot.blue::after{background:#1e88e5}
.assist{left:675px;top:597px;width:209px;height:223px;border:1px solid #dfe5ea}
.assist h3{font-family:"Crimson Text",Georgia,serif;font-weight:600;font-size:16px;color:var(--brand-dark);padding:0 15px;height:27px;line-height:27px;background:linear-gradient(#fff,#f0f4f7);border-bottom:1px solid #dfe5ea}
.field{position:absolute;left:10px;font-size:9px;color:#333;display:flex;align-items:center}
.field label{width:49px}
.field input{width:142px;height:16px;border:1px solid #dbe0e4;background:#fff}
.msg{position:absolute;left:12px;top:140px;width:190px;height:50px;border:1px solid #dbe0e4}
.submit{position:absolute;right:6px;top:196px;width:57px;height:18px;background:var(--accent);color:#fff;font-size:9.5px;font-weight:700;display:flex;align-items:center;justify-content:center;border-radius:2px}
.testi-title{left:173px;top:665px;font-family:"Crimson Text",Georgia,serif;font-weight:600;font-size:17px;color:var(--brand-dark)}
.quote{left:167px;top:695px;width:216px;height:98px;background:#ededed;border-radius:5px;padding:12px 10px;font-family:"Crimson Text",Georgia,serif;font-style:italic;font-size:13px;line-height:17px;color:#444}
.author{left:320px;top:801px;font-size:9px;color:#222;line-height:12px}
.author b{display:block;font-weight:700}
.author i{font-style:italic}
.events{left:419px;top:664px;width:210px;height:149px;border:1px solid #dfe5ea}
.events h3{font-family:"Crimson Text",Georgia,serif;font-weight:600;font-size:15px;color:var(--brand-dark);padding:0 16px;height:25px;line-height:25px;background:linear-gradient(#fff,#eef3f7);border-bottom:1px solid #dfe5ea}
.event{position:absolute;left:6px;display:flex;gap:10px}
.event .thumb{width:64px;height:43px;background:linear-gradient(#c2473c,#e8d8d0 55%,#b44a3e)}
.event p{width:120px;font-size:8px;line-height:13.5px;color:#999}
.partners{left:167px;top:834px;width:717px;height:107px;border:1px solid #cfd6dc}
.partners .tag{position:absolute;left:5px;top:4px;width:22px;height:97px;background:var(--accent);color:#fff;font-family:"Crimson Text",Georgia,serif;font-size:12px;letter-spacing:1px;writing-mode:vertical-rl;transform:rotate(180deg);display:flex;align-items:center;justify-content:center}
.badge{position:absolute;top:18px;width:80px;height:70px;background:#2b2b2b;border-radius:4px}
.footer-band{left:0;top:957px;width:1050px;height:243px;background:var(--footer-bg)}
.footer-mid{left:151px;top:957px;width:751px;height:243px;background:var(--footer-mid)}
.footer-panel{left:165px;top:978px;width:721px;height:116px;background:var(--footer-panel);border:1px solid #083a78;border-radius:4px}
.fcol{position:absolute;top:12px;font-size:9.5px;color:#a9c7ea;line-height:15.5px}
.fcol h4{color:#fff;font-size:10px;font-weight:700;margin-bottom:14px}
.social{position:absolute;width:20px;height:20px;border-radius:50%;background:#e9eef5}
.footer-links{left:185px;top:1094px;width:687px;height:39px;background:var(--footer-panel);display:flex;align-items:center;justify-content:center;gap:14px;font-size:9.5px;color:#d8e6f6}
.copyright{left:151px;top:1147px;width:751px;text-align:center;font-size:9px;color:#d8e6f6}
</style>
</head>
<body>
<div class="abs topline"></div>
<div class="abs page"></div>

<nav class="abs main-nav">
  <a style="width:76px">HOME</a><a style="width:77px">ABOUT</a><a style="width:101px">COURSES</a><a style="width:114px">DOCTOR NAME</a><a style="width:91px">FACULTY</a><a style="width:69px">FAQ</a><a style="width:97px">PATIENTS</a><a style="width:126px;border-right:0">CONTACT</a>
</nav>

<header class="abs header">
  <div class="abs brand"><i></i>Mavolix</div>
  <div class="abs call"><small>CALL FOR INQUIRIES!</small><strong>123 456 7890</strong></div>
</header>

<nav class="abs course-nav">
  <a class="active"><svg viewBox="0 0 10 12"><path d="M2 1l6 5-6 5" fill="none" stroke="#fff" stroke-width="2.4"/></svg>Course 1</a>
  <a><svg viewBox="0 0 10 12"><path d="M2 1l6 5-6 5" fill="none" stroke="#fff" stroke-width="2.4"/></svg>Course 2</a>
  <a><svg viewBox="0 0 10 12"><path d="M2 1l6 5-6 5" fill="none" stroke="#fff" stroke-width="2.4"/></svg>Course 3</a>
  <a><svg viewBox="0 0 10 12"><path d="M2 1l6 5-6 5" fill="none" stroke="#fff" stroke-width="2.4"/></svg>Course 4</a>
  <a><svg viewBox="0 0 10 12"><path d="M2 1l6 5-6 5" fill="none" stroke="#fff" stroke-width="2.4"/></svg>Course 5</a>
  <a><svg viewBox="0 0 10 12"><path d="M2 1l6 5-6 5" fill="none" stroke="#fff" stroke-width="2.4"/></svg>Course 6</a>
  <a style="border-bottom:0"><svg viewBox="0 0 10 12"><path d="M2 1l6 5-6 5" fill="none" stroke="#fff" stroke-width="2.4"/></svg>Course 7</a>
</nav>
<div class="abs hero" role="img" aria-label="Smiling group of dental students"></div>

<div class="abs news"><h3>NEWS:</h3><p>Lorem ipsum dolor sit amet, consectetuer adipiscing elit. Aenean commodo ligula eget dolor.Lorem ipsum dolor sit amet,</p></div>

<h2 class="abs welcome-title">WELCOME</h2>
<p class="abs welcome-copy">Lorem ipsum dolor sit amet, consectetuer adipiscing elit. Aeneacommodo ligula eget dolor.Lorem ipsum dolor sit amet, consectetuer adipiscing elit. AenLorem ipsum dolor sitmet, consectetuer adipiscing elit. ean commodo ligula eget dolor.ean commodo ligulat dolor.Loreor sit amet, consectetuer adipiscing elit. Aenean commodo ligulegLoremet, consectetuer adipiscing elit. Aenean commodo ligula eget doLorem ipsum dolor sit amet, coscing elit. Aenean commodo ligula eget dolor.lor.g elit. Aenean commodo ligula eget dolor.Lorem ipsum dolor sit amet, cctetuer adipiscing elit. AeLoLorem ipsuing elit. Aenean commoan commodo ligula eget dolor.ean commodo ligulat dolor.Lorem ipsum dolor sit amet,</p>
<div class="abs doctor-photo"><div role="img" aria-label="Doctor examining a young patient"></div></div>
<div class="abs btn-read">Read more</div>
<div class="abs hr"></div>
<div class="abs vr"></div>

<div class="abs calendar">
  <div class="cal-head"><span>◂</span><span>April 2011</span><span>▸</span></div>
  <div class="cal-days"><span>MON</span><span>TUE</span><span>WED</span><span>THU</span><span>FRI</span><span>SAT</span><span>SUN</span></div>
  <div class="cal-grid">
    <span class="off">28</span><span class="off">29</span><span class="off">30</span><span class="off">31</span><span>1</span><span>2</span><span>3</span>
    <span class="today">4</span><span>5</span><span class="sel">6</span><span>7</span><span class="dot">8</span><span>9</span><span>10</span>
    <span>11</span><span>12</span><span>13</span><span>14</span><span>15</span><span class="dot blue">16</span><span>17</span>
    <span>18</span><span>19</span><span>20</span><span>21</span><span>22</span><span>23</span><span>24</span>
    <span>25</span><span>26</span><span>27</span><span>28</span><span>29</span><span>30</span><span class="off">1</span>
  </div>
</div>

<form class="abs assist">
  <h3>Need Assistance?</h3>
  <div class="field" style="top:38px"><label>Name</label><input type="text"></div>
  <div class="field" style="top:60px"><label>email ID</label><input type="text"></div>
  <div class="field" style="top:82px"><label>phone no</label><input type="text"></div>
  <div class="field" style="top:104px"><label>Address</label><input type="text"></div>
  <div class="field" style="top:124px"><label>Messagebox</label></div>
  <div class="msg"></div>
  <div class="submit">Submit</div>
</form>

<h3 class="abs testi-title">Testimonials</h3>
<blockquote class="abs quote">Lorem ipsum dolor sit amet, consectetuer adipiscing elit. Aenean commodo ligula eget dolor. Aenean massa. Cum sociis natoque"</blockquote>
<div class="abs author"><b>Marlo</b><i>Marlo student</i></div>

<section class="abs events">
  <h3>News &amp; Events</h3>
  <div class="event" style="top:32px"><div class="thumb" role="img" aria-label="Close-up of a smile"></div><p>Lorem ipsum dolor sit amet, consectetuer adipiscing elit. Aenean commodo ligula eget dolor.</p></div>
  <div class="event" style="top:89px"><div class="thumb" role="img" aria-label="Close-up of a smile"></div><p>Lorem ipsum dolor sit amet, consectetuer adipiscing elit. Aenean commodo ligula eget dolor.</p></div>
</section>

<section class="abs partners">
  <div class="tag">UNIVERSITIES</div>
  <div class="badge" style="left:58px"></div>
  <div class="badge" style="left:193px"></div>
  <div class="badge" style="left:328px"></div>
  <div class="badge" style="left:464px"></div>
  <div class="badge" style="left:599px"></div>
</section>

<div class="abs footer-band"></div>
<div class="abs footer-mid"></div>
<footer class="abs footer-panel">
  <div class="fcol" style="left:32px"><h4>Company</h4>About us<br>Vision<br>Team<br>Success Stories</div>
  <div class="fcol" style="left:159px"><h4>Student</h4>Tests<br>Educational Loans<br>Faqs</div>
  <div class="fcol" style="left:287px"><h4>Why us</h4>Why Choose Us<br>Testimonials<br>Press Clips<br>Photo Gallery</div>
  <div class="fcol" style="left:410px"><h4>Online</h4>Enquiry<br>Registration<br>Feedback</div>
  <div class="fcol" style="left:513px;width:100px"><h4>Contacts</h4><span style="line-height:15px">Lorem ipsum dolor sit amet, consectetuer adipiscing elit. Aenean commodo</span></div>
  <div class="fcol" style="left:631px"><h4>Follow Us</h4></div>
  <span class="social" style="left:633px;top:40px"></span>
  <span class="social" style="left:667px;top:40px"></span>
  <span class="social" style="left:633px;top:75px"></span>
  <span class="social" style="left:667px;top:75px"></span>
</footer>
<nav class="abs footer-links"><span>Home</span>|<span>About</span>|<span>Courses</span>|<span>Doctor Name</span>|<span>Faculty</span>|<span>FAQ</span>|<span>Patients</span>|<span>Contact</span></nav>
<p class="abs copyright">Dental Website Design – Copyright © 2012</p>
</body>
</html>
```